Construction company business card

One side to be the logo with the company name, The other side I would like: (Tomas verbick) Project manager 41 barrow crescent hallam 52917306224783(03) 9703 2428Info@gudeljgroup.comAnd then maybe a couple dot points saying what we do:Construction (commercial & industrial) Civil construction

Anything else please contact me!
Maybe curved st one edge of the card

Target Market(s)

Older clientele

Industry/Entity Type

Construction Company

Contact Information for Business Card

Read above

Colors
3277b5
1b1b1b
9d9d9d

Requirements
Must have
• Use my logo on one side
Nice to have
• Read above
Should not have
• Read above

```html
<!DOCTYPE html>
<html lang="en">
<head>
<meta charset="utf-8">
<title>Stonefield Property Group – Business Card</title>
<link href="https://fonts.googleapis.com/css2?family=Open+Sans:wght@400;700&display=swap" rel="stylesheet">
<style>
  :root {
    --brand-blue: #3277b5;
    --brand-black: #1b1b1b;
    --brand-grey: #9d9d9d;
    --ink: #4a4a4a;
    --paper: #ffffff;
    --backdrop: #d6d6d6;
    --faint-blue: #e4edf5;
  }
  * { box-sizing: border-box; margin: 0; padding: 0; }
  html, body { width: 1200px; height: 900px; overflow: hidden; }
  body {
    background: var(--backdrop);
    font-family: "Open Sans", Arial, sans-serif;
    position: relative;
  }
  .card {
    position: absolute;
    width: 600px;
    height: 340px;
    box-shadow: 0 6px 18px rgba(0,0,0,.18);
    overflow: hidden;
  }
  .card--front {
    left: 150px; top: 70px;
    background: var(--brand-black);
    border-radius: 170px 0 0 170px;
  }
  .front__brand {
    position: absolute; left: 70px; top: 100px;
    display: flex; align-items: center; gap: 26px;
  }
  .brand-dot {
    width: 130px; height: 130px; border-radius: 50%;
    background: var(--brand-blue);
    flex: none;
  }
  .brand-name {
    color: var(--brand-blue);
    font-weight: 700;
    text-transform: uppercase;
    letter-spacing: 2px;
    line-height: 1.15;
  }
  .card--front .brand-name { font-size: 30px; }
  .front__services {
    position: absolute; right: 40px; bottom: 40px;
    list-style: none; text-align: right;
    color: #e6e6e6; font-size: 15px; line-height: 1.5;
  }
  .card--back {
    left: 450px; top: 490px;
    background: var(--paper);
    border-radius: 0 170px 170px 0;
  }
  .back__decor {
    position: absolute; right: 30px; top: 30px;
    width: 280px; height: 280px; border-radius: 50%;
    background: var(--faint-blue);
  }
  .back__person {
    position: absolute; right: 70px; top: 140px; width: 240px;
    text-align: center;
  }
  .person__name {
    color: var(--brand-blue); font-weight: 700; font-size: 21px;
    text-transform: uppercase; letter-spacing: .5px;
  }
  .person__role { color: var(--ink); font-size: 15px; }
  .back__brand {
    position: absolute; left: 34px; top: 34px;
    display: flex; align-items: center; gap: 12px;
  }
  .back__brand .brand-dot { width: 52px; height: 52px; }
  .card--back .brand-name { font-size: 15px; letter-spacing: 1px; }
  .back__contact {
    position: absolute; left: 34px; bottom: 30px;
    color: var(--ink); font-size: 14px; line-height: 1.45;
  }
  .contact__address { margin-bottom: 10px; }
  .contact__list { list-style: none; }
  .contact__list li { display: flex; align-items: center; gap: 8px; }
  .contact__list svg { width: 13px; height: 13px; flex: none; }
</style>
</head>
<body>
  <section class="card card--front" aria-label="Card front">
    <div class="front__brand">
      <span class="brand-dot"></span>
      <p class="brand-name">Stonefield<br>Property Group</p>
    </div>
    <ul class="front__services">
      <li>Construction (Commercial &amp; Industrial)</li>
      <li>Civil Construction</li>
    </ul>
  </section>

  <section class="card card--back" aria-label="Card back">
    <span class="back__decor"></span>
    <div class="back__person">
      <p class="person__name">Tomas Verbick</p>
      <p class="person__role">Project Manager</p>
    </div>
    <div class="back__brand">
      <span class="brand-dot"></span>
      <p class="brand-name">Stonefield<br>Property Group</p>
    </div>
    <div class="back__contact">
      <p class="contact__address">41 Barrow Crescent<br>Ashvale 5291</p>
      <ul class="contact__list">
        <li><svg viewBox="0 0 16 16" aria-hidden="true"><path fill="#3277b5" d="M3 1l3 3-2 2c1 2 3 4 5 5l2-2 3 3-2 3C6 15 1 10 0 4z"/></svg>(03) 9418 6573</li>
        <li><svg viewBox="0 0 16 16" aria-hidden="true"><rect x="4" y="1" width="8" height="14" rx="1.5" fill="none" stroke="#3277b5" stroke-width="1.6"/></svg>730 622 4783</li>
        <li><svg viewBox="0 0 16 16" aria-hidden="true"><rect x="1" y="3" width="14" height="10" fill="none" stroke="#3277b5" stroke-width="1.6"/><path d="M1 3l7 6 7-6" fill="none" stroke="#3277b5" stroke-width="1.6"/></svg>Info@verbickgroup.com</li>
        <li><svg viewBox="0 0 16 16" aria-hidden="true"><circle cx="8" cy="8" r="7" fill="none" stroke="#3277b5" stroke-width="1.6"/><path d="M1 8h14M8 1c-3 4-3 10 0 14M8 1c3 4 3 10 0 14" fill="none" stroke="#3277b5" stroke-width="1.2"/></svg>www.verbickgroup.com</li>
      </ul>
    </div>
  </section>
</body>
</html>
```